The Copperline Collective's website for high impact furniture promotions

I am looking for a simple website. we are a promotional company that runs events for furniture stores to increase sales for short periods of time. i would like the website to have about 4 areas to explain our company. I would like it to be simple and user friendly. I would like a link to chatterbook and a contact section. I am attaching our logo that i would like somewhere large or possibly in the backround. I am open to different color schemes. I would like to convey fast paced, modern, reliable. I am open to all different styles and look forward to seeing whats out there. we are looking for a quick turn around, so if we see one that we like quick, we will pick that one thanks
Reason: looking for some really creative designs and want to give a fair amount of time to produce
Target Market(s)
Retail Furniture store owners
Industry/Entity Type
It Company
Number of Pages Required
1 page
Colors
Designer to choose colors to be used in the design.
Look and feel

```html
<!DOCTYPE html>
<html lang="en">
<head>
<meta charset="utf-8">
<title>The Copperline Collective</title>
<link href="https://fonts.googleapis.com/css2?family=Roboto:wght@400;500;700&family=Raleway:wght@500;600;700&family=Poppins:wght@400;500&display=swap" rel="stylesheet">
<style>
:root{
  --copper:#c08a52;
  --beige:#e7cc9f;
  --ink:#2e2e2e;
  --text:#555;
  --muted:#7a7a7a;
  --card:#efeeee;
  --light:#f2f2f2;
  --dark:#262626;
  --field:#5a5a5a;
  --white:#fff;
}
*{margin:0;padding:0;box-sizing:border-box}
html,body{width:1200px;height:3346px;overflow:hidden;background:var(--white)}
body{font-family:"Roboto",sans-serif;color:var(--ink);position:relative}
section,header,footer{position:absolute;left:0;width:1200px}
.abs{position:absolute}
.center{left:0;width:1200px;text-align:center}

/* hero */
.hero{top:0;height:551px}
.hero-photo{position:absolute;inset:0;background:linear-gradient(135deg,#4c5257 0%,#6d6c68 45%,#8a8680 70%,#cfcac2 100%)}
.hero-shade{position:absolute;inset:0;background:rgba(20,20,20,.35)}
.topbar{top:0;height:80px;background:rgba(15,15,15,.78);z-index:2}
.brand{left:100px;top:14px;display:flex;align-items:center;gap:14px}
.brand-dot{width:52px;height:52px;border-radius:50%;background:var(--copper)}
.brand-name{font-family:"Raleway",sans-serif;font-weight:600;font-size:20px;color:var(--white);letter-spacing:1px}
.nav a{position:absolute;top:29px;font-size:16px;color:var(--white);text-decoration:none}
.nav .active::after{content:"";position:absolute;left:-14px;right:-14px;top:44px;height:5px;background:var(--copper)}
.hero h1{top:232px;font-size:56px;font-weight:700;color:var(--white);letter-spacing:1px}
.hero .tag{font-size:30px;font-weight:500;color:var(--white);line-height:49px;top:313px}

/* what we do */
.what{top:551px;height:497px}
.sec-title{font-family:"Raleway",sans-serif;font-weight:600;font-size:28px;color:var(--ink)}
.what .sec-title{top:50px;letter-spacing:1px}
.rule{height:3px;width:40px;background:var(--copper);left:580px}
.what .lead{top:124px;font-family:"Poppins",sans-serif;font-size:12.5px;line-height:29px;color:var(--text)}
.card{top:243px;width:294px;height:201px;background:var(--card);text-align:center}
.card .icon{position:absolute;left:116px;top:-31px;width:62px;height:62px;border-radius:50%;background:var(--beige);display:flex;align-items:center;justify-content:center}
.card h3{margin-top:62px;font-family:"Raleway",sans-serif;font-weight:500;font-size:16px;color:var(--ink)}
.card p{margin:28px 22px 0;font-family:"Poppins",sans-serif;font-size:12px;line-height:24.5px;color:var(--muted)}

/* banner */
.banner{top:1048px;height:433px}
.banner-photo{position:absolute;inset:0;background:linear-gradient(160deg,#3b3a3d 0%,#5b5657 40%,#46434a 70%,#2f2d30 100%)}
.banner-shade{position:absolute;inset:0;background:rgba(20,20,20,.35)}
.banner h2{top:110px;font-size:38px;font-weight:500;color:var(--white)}
.banner .tag{top:190px;font-size:20px;font-weight:500;color:var(--white);line-height:45px}
.btn-copper{left:435px;top:306px;width:328px;height:49px;background:var(--copper);color:var(--white);font-size:21px;display:flex;align-items:center;justify-content:center;text-decoration:none;letter-spacing:.5px}

/* story */
.story{top:1481px;height:482px;background:var(--light)}
.story-card{left:212px;top:69px;width:776px;height:344px;background:var(--white);box-shadow:0 6px 18px rgba(0,0,0,.18)}
.story-photo{position:absolute;left:0;top:0;width:355px;height:344px;background:linear-gradient(120deg,#e6e7e5 0%,#cfd0cf 50%,#9a9ea3 100%)}
.story h2{left:404px;top:50px;font-family:"Raleway",sans-serif;font-weight:500;font-size:24px}
.story p{left:404px;top:100px;width:340px;font-family:"Poppins",sans-serif;font-size:12px;line-height:28.5px;color:var(--text)}
.btn-dark{left:404px;top:263px;width:149px;height:40px;background:var(--ink);color:var(--white);font-size:15px;display:flex;align-items:center;justify-content:center;text-decoration:none}

/* responsibility */
.resp{top:1963px;height:314px}
.resp h2{left:132px;top:82px;font-size:21px;font-weight:500;line-height:43px;color:var(--ink)}
.resp p{left:500px;top:80px;width:590px;font-family:"Poppins",sans-serif;font-size:11.5px;line-height:24.6px;color:var(--text)}

/* events */
.events{top:2277px;height:547px;background:#f4f4f4}
.events .sec-title{top:58px;font-family:"Roboto",sans-serif;font-weight:500;font-size:29px}
.event{top:132px;width:321px}
.event .photo{height:225px}
.event h3{margin-top:24px;font-size:16px;font-weight:500;color:var(--ink)}
.event p{margin-top:12px;font-family:"Poppins",sans-serif;font-size:11.5px;line-height:24.5px;color:var(--text)}

/* contact */
.contact{top:2824px;height:522px;background:var(--dark);color:var(--white)}
.contact .sec-title{top:30px;font-family:"Roboto",sans-serif;font-weight:500;font-size:32px;color:var(--white)}
.contact .rule2{left:524px;top:87px;width:152px;height:1px;background:#888}
.map{left:167px;top:143px;width:371px;height:272px;background:linear-gradient(135deg,#b9b6ad 0%,#a8aab0 45%,#7d93b6 100%)}
.map-shade{position:absolute;inset:0;background:rgba(40,40,40,.35)}
.map h3{position:absolute;left:0;width:100%;top:53px;text-align:center;font-size:21px;font-weight:500}
.info{position:absolute;left:60px;display:flex;align-items:center;gap:18px;font-size:16.5px;letter-spacing:.5px}
.info svg{width:20px;height:20px;flex:none}
.form-title{left:700px;top:104px;font-size:17px;color:#e8e8e8}
.field{left:700px;width:357px;background:var(--field);color:#e2e2e2;font-size:12px;padding:10px 12px;font-family:"Roboto",sans-serif}
.btn-outline{left:700px;top:399px;width:357px;height:38px;border:2px solid var(--white);color:var(--white);font-size:16px;font-weight:500;display:flex;align-items:center;justify-content:center;letter-spacing:.5px;text-decoration:none}
.copy{left:98px;top:478px;font-size:12px;font-weight:500;color:#ddd}
.social{left:1040px;top:471px;display:flex;align-items:center;gap:8px;font-size:12px;color:#ddd;text-decoration:none}
.social span.dot{width:16px;height:16px;border-radius:50%;background:#ddd}
</style>
</head>
<body>

<header class="topbar">
  <div class="abs brand"><span class="brand-dot"></span><span class="brand-name">The Copperline Collective</span></div>
  <nav class="nav">
    <a class="active" style="left:518px">Home</a>
    <a style="left:640px">About Us</a>
    <a style="left:777px">Services</a>
    <a style="left:909px">Projects</a>
    <a style="left:1043px">Contact</a>
  </nav>
</header>

<section class="hero">
  <div class="hero-photo" role="img" aria-label="Photo of a bright living room with a white sofa, shelves and a chalkboard wall"></div>
  <div class="hero-shade"></div>
  <h1 class="abs center">ASK, LISTEN AND ACT</h1>
  <p class="abs center tag">Better Than Any Others, These Three Words<br>Summarize Success In Sales</p>
</section>

<section class="what">
  <h2 class="abs center sec-title">WHAT WE DO</h2>
  <div class="abs rule" style="top:94px"></div>
  <p class="abs center lead">Neque porro quisquam est qui dolorem ipsum quia dolor sit amet, consectetur, adipisci velit<br>qui dolorem ipsum quia dolor sit amet, consectetur, adipisci velit</p>

  <div class="abs card" style="left:136px">
    <div class="icon"><svg width="30" height="30" viewBox="0 0 24 24" fill="#2e2e2e"><circle cx="9" cy="13" r="5"/><circle cx="9" cy="13" r="2" fill="#e7cc9f"/><circle cx="17" cy="7" r="3.5"/><circle cx="17" cy="7" r="1.3" fill="#e7cc9f"/></svg></div>
    <h3>On Time Service</h3>
    <p>Neque porro quisquam est qui dolorem ipsum quia dolor sit amet, consectetur, adipisci velit</p>
  </div>
  <div class="abs card" style="left:455px">
    <div class="icon"><svg width="30" height="30" viewBox="0 0 24 24" fill="#2e2e2e"><circle cx="12" cy="8" r="5"/><path d="M3 22c0-5 4-8 9-8s9 3 9 8z"/></svg></div>
    <h3>Talent Team</h3>
    <p>Neque porro quisquam est qui dolorem ipsum quia dolor sit amet, consectetur, adipisci velit</p>
  </div>
  <div class="abs card" style="left:774px">
    <div class="icon"><svg width="28" height="28" viewBox="0 0 24 24" fill="none" stroke="#2e2e2e" stroke-width="2" stroke-linejoin="round"><path d="M3 11h4v10H3zM7 11l4-8c2 0 2 2 2 3v3h6c1 0 2 1 2 2l-2 8c0 1-1 2-2 2H7"/></svg></div>
    <h3>Customer Satisfaction</h3>
    <p>Neque porro quisquam est qui dolorem ipsum quia dolor sit amet, consectetur, adipisci velit</p>
  </div>
</section>

<section class="banner">
  <div class="banner-photo" role="img" aria-label="Photo of a dark lounge with a grey sofa, vases and a floor lamp"></div>
  <div class="banner-shade"></div>
  <h2 class="abs center">Create And Maintain Favorable Attention</h2>
  <p class="abs center tag">Effective Marketing, Referrals, Strong Sales Skills, And Strategic Questions<br>Are The Keys To Creating Favorable Attention</p>
  <a class="abs btn-copper" href="#contact">CONTACT US TODAY</a>
</section>

<section class="story">
  <div class="abs story-card">
    <div class="story-photo" role="img" aria-label="Portrait photo of a smiling businessman in a grey suit"></div>
    <h2 class="abs">Our Story</h2>
    <p class="abs">Neque porro quisquam est qui dolorem ipsum quia dolor sit amet, consectetur, adipisci velitNeque porro quisquam est qui dolorem ipsum quia dolor sit amet, consectetur, adipisci velitipsum quia dolor sit amet, consectetur, adipisci velit</p>
    <a class="abs btn-dark" href="#">Read More</a>
  </div>
</section>

<section class="resp">
  <h2 class="abs">Take The Responsibility<br>But Not The Credit</h2>
  <p class="abs">Lorem Ipsum is simply dummy text of the printing and typesetting industry. Lorem Ipsum has been the industry's standard dummy text ever since the 1500s, when an unknown printer took a galley of type and scrambled it to make a type specimen book. It has survived not only five centuries, but also the leap into electronic typesetting, remaining essentially unchanged. It was popularised in the 1960s with the release of Letraset It has survived not only five centuries, but also the leap into electronic typesetting, remaining essentially unchanged. It was popularised in the 1960s with the release of Letraset</p>
</section>

<section class="events">
  <h2 class="abs center sec-title">Upcoming Events</h2>
  <article class="abs event" style="left:98px">
    <div class="photo" role="img" aria-label="Photo of a man carrying a cushion through a furniture showroom" style="background:linear-gradient(135deg,#8c8a88,#5b5a5c 60%,#a7a3a0)"></div>
    <h3>Neque porro quisquam est qui dolorem</h3>
    <p>Lorem Ipsum is simply dummy text of the printing and typ esetting industry. Lorem Ipsum has been the industry's standard dummy text ever since the 1500s</p>
  </article>
  <article class="abs event" style="left:439px">
    <div class="photo" role="img" aria-label="Photo of a bright living room with a grey sofa and patterned cushions" style="background:linear-gradient(135deg,#cfd1d2,#b2b6b8 55%,#d8cbbb)"></div>
    <h3>Neque porro quisquam est qui dolorem</h3>
    <p>Lorem Ipsum is simply dummy text of the printing and typ esetting industry. Lorem Ipsum has been the industry's standard dummy text ever since the 1500s</p>
  </article>
  <article class="abs event" style="left:781px">
    <div class="photo" role="img" aria-label="Photo of a garden patio with wicker seating and cushions" style="background:linear-gradient(135deg,#6f8a4a,#a89a73 55%,#c9b99a)"></div>
    <h3>Neque porro quisquam est qui dolorem</h3>
    <p>Lorem Ipsum is simply dummy text of the printing and typ esetting industry. Lorem Ipsum has been the industry's standard dummy text ever since the 1500s</p>
  </article>
</section>

<footer class="contact" id="contact">
  <h2 class="abs center sec-title">Get In Touch</h2>
  <div class="rule2 abs"></div>

  <div class="abs map" role="img" aria-label="Street map of the office area">
    <div class="map-shade"></div>
    <h3>Contact Us</h3>
    <div class="info" style="top:112px"><svg viewBox="0 0 24 24" fill="#fff"><path d="M2 11L22 2l-9 20-2-9z"/></svg>418 Harrow Lane , 70999</div>
    <div class="info" style="top:157px"><svg viewBox="0 0 24 24" fill="#fff"><path d="M6 2h4l2 5-3 2c1 3 3 5 6 6l2-3 5 2v4c0 2-2 4-4 4C10 22 2 14 2 6c0-2 2-4 4-4z"/></svg>555 0142 7780, 555 0198 3321</div>
    <div class="info" style="top:197px"><svg viewBox="0 0 24 24" fill="#fff"><path d="M2 5h20v14H2z"/><path d="M2 5l10 8 10-8" fill="none" stroke="#555" stroke-width="1.6"/></svg>hello@copperline.example</div>
  </div>

  <p class="abs form-title">Send Us A Message</p>
  <div class="abs field" style="top:147px;height:36px">Name</div>
  <div class="abs field" style="top:210px;height:35px">Email</div>
  <div class="abs field" style="top:270px;height:107px">Message</div>
  <a class="abs btn-outline" href="#">SEND US TODAY</a>

  <p class="abs copy">© 2017 The Copperline Collective. All Rights Reserved.</p>
  <a class="abs social" href="#"><span class="dot"></span>chatterbook</a>
</footer>

</body>
</html>
```